We are a recruitment company based in Norwich/Cambridge England.
I have included our company logo which we want to remain the same.

What we are looking for is a new creative Business card which will really stand out!!

Contact Information for Business Card

Harriet Dunmore
email: Harriet@plavex.co.uk
Address: Brackwell House
Fenmoor Enterprise Park
Partridge Way
Norwich
QB9 3KX
Tel:01632 960418

```html
<!DOCTYPE html>
<html lang="en">
<head>
<meta charset="utf-8">
<title>Plavex Business Card</title>
<link rel="stylesheet" href="https://fonts.googleapis.com/css2?family=Lato:wght@300;400;700&display=swap">
<style>
  :root {
    --brand-green: #8bc13f;
    --ink: #4a4a4c;
    --rule: #3d3d3f;
    --card-white: #ffffff;
    --backdrop: #e9e9e7;
  }
  * { margin: 0; padding: 0; box-sizing: border-box; }
  html, body { width: 1200px; height: 1200px; overflow: hidden; }
  body {
    background: var(--backdrop);
    font-family: "Lato", Arial, sans-serif;
    color: var(--ink);
    display: flex;
    flex-direction: column;
    align-items: center;
    justify-content: center;
    gap: 60px;
  }
  .card {
    width: 900px;
    height: 520px;
    position: relative;
    box-shadow: 0 6px 20px rgba(0,0,0,0.12);
  }
  .card-front {
    background: var(--brand-green);
    display: flex;
    align-items: center;
    justify-content: center;
  }
  .brand-lockup {
    display: flex;
    align-items: center;
    gap: 26px;
  }
  .brand-dot {
    width: 120px;
    height: 120px;
    border-radius: 50%;
    background: var(--card-white);
  }
  .brand-name {
    font-weight: 700;
    font-size: 110px;
    color: var(--card-white);
    letter-spacing: -1px;
  }
  .card-back { background: var(--card-white); }
  .rule {
    position: absolute;
    left: 80px;
    right: 80px;
    height: 2px;
    background: var(--rule);
  }
  .rule-top { top: 170px; }
  .rule-bottom { top: 330px; }
  .back-brand {
    position: absolute;
    top: 70px;
    left: 0;
    right: 0;
    display: flex;
    justify-content: center;
    align-items: center;
    gap: 16px;
  }
  .back-brand .mark {
    width: 64px;
    height: 64px;
    border-radius: 50%;
    background: var(--brand-green);
  }
  .back-brand .name {
    font-weight: 700;
    font-size: 48px;
    color: var(--ink);
  }
  .contact-band {
    position: absolute;
    top: 172px;
    left: 90px;
    right: 90px;
    height: 156px;
    display: flex;
    justify-content: space-between;
    align-items: flex-start;
    gap: 40px;
  }
  .person-name {
    margin-top: 28px;
    font-weight: 400;
    font-size: 44px;
    line-height: 1.1;
    color: var(--ink);
    white-space: nowrap;
  }
  .contact-list {
    margin-top: 48px;
    list-style: none;
    font-size: 32px;
    font-weight: 400;
    white-space: nowrap;
  }
  .contact-list li {
    display: flex;
    align-items: center;
    gap: 14px;
    line-height: 1.3;
  }
  .contact-list svg { width: 24px; height: 24px; fill: var(--ink); flex: none; }
  .web-address {
    position: absolute;
    top: 352px;
    left: 0; right: 0;
    text-align: center;
    font-size: 40px;
  }
  .postal-address {
    position: absolute;
    top: 416px;
    left: 0; right: 0;
    text-align: center;
    font-size: 26px;
    line-height: 1.35;
    font-weight: 400;
  }
</style>
</head>
<body>
  <section class="card card-front">
    <div class="brand-lockup">
      <span class="brand-dot"></span>
      <span class="brand-name">Plavex</span>
    </div>
  </section>

  <section class="card card-back">
    <div class="back-brand">
      <span class="mark"></span>
      <span class="name">Plavex</span>
    </div>
    <div class="rule rule-top"></div>
    <div class="contact-band">
      <h1 class="person-name">Harriet Dunmore</h1>
      <ul class="contact-list">
        <li>
          <svg viewBox="0 0 24 24" aria-hidden="true"><path d="M6.6 10.8a15.1 15.1 0 0 0 6.6 6.6l2.2-2.2a1 1 0 0 1 1-.25 11.4 11.4 0 0 0 3.6.57 1 1 0 0 1 1 1V20a1 1 0 0 1-1 1A17 17 0 0 1 3 4a1 1 0 0 1 1-1h3.5a1 1 0 0 1 1 1 11.4 11.4 0 0 0 .57 3.6 1 1 0 0 1-.25 1z"/></svg>
          01632 960418
        </li>
        <li>
          <svg viewBox="0 0 24 24" aria-hidden="true"><path d="M2 5h20v14H2z M3.5 6.5 12 13l8.5-6.5" fill="none" stroke="#4a4a4c" stroke-width="2"/></svg>
          Harriet@plavex.co.uk
        </li>
      </ul>
    </div>
    <div class="rule rule-bottom"></div>
    <p class="web-address">www.plavex.co.uk</p>
    <p class="postal-address">Brackwell House, Fenmoor Enterprise Park, Partridge Way,<br>Norwich, QB9 3KX</p>
  </section>
</body>
</html>
```